Quick Straightforward Billboard Redesign

- Design billboard sized for 10 foot' x 36' foot width live area size and please include bleeds 6" around all sides
- Exact blue color match is imperative in headline, logo, phone number bubble or wherever used. C-83 / M-45 / Y-1 / K-0-
- What I hope to illustrate is that our company offers the best porch screening in the area area, in regards to quality, expertise, durability, storms proof, but we do not build screen porches.
- Current board is attached below from previous designer, and as you can see sizing was off, white space on edges make it appear to be sized incorrectly.
- I also attached my own little mock up idea well well if it helps, favorite image, logo, headline, etc and ideas perhaps on expanding or making this better?

Thanks so much!

Target Market(s)

Drivers and passengers, Southeastern NC, are of immense new construction and high end homes.

Industry/Entity Type

Construction

Colors
0054AA
0677BA
7BADD7
CADEEF
E8F1F8

Requirements
Must have
• Blue color matching
Nice to have
• Design spins or other thoughts on my little mock up

```html
<!DOCTYPE html>
<html lang="en">
<head>
<meta charset="UTF-8">
<title>Coastwise Screening Billboard</title>
<link href="https://fonts.googleapis.com/css2?family=Antonio:wght@700&family=Montserrat:wght@800&display=swap" rel="stylesheet">
<style>
  :root {
    --brand-blue: #3f7bbf;
    --brand-green: #5bae4e;
    --paper: #ffffff;
    --sky-light: #e8f1f8;
    --sky-mid: #cadeef;
    --lawn: #a9c98a;
    --lake: #7badd7;
  }
  html, body {
    margin: 0;
    padding: 0;
    width: 1200px;
    height: 347px;
    overflow: hidden;
    background: var(--paper);
  }
  .billboard {
    display: block;
    width: 1200px;
    height: 347px;
  }
  .headline-band { fill: var(--brand-blue); }
  .accent-stripe { fill: var(--brand-green); }
  .contact-band { fill: var(--brand-blue); }
  .headline {
    font-family: "Antonio", "Arial Narrow", sans-serif;
    font-weight: 700;
    font-size: 92px;
    fill: var(--paper);
  }
  .tagline {
    font-family: "Montserrat", Arial, sans-serif;
    font-weight: 800;
    font-size: 34px;
    fill: var(--paper);
  }
  .company-name {
    font-family: "Antonio", "Arial Narrow", sans-serif;
    font-weight: 700;
    font-size: 56px;
    fill: var(--brand-blue);
  }
  .company-mark { fill: var(--brand-blue); }
  .phone-number {
    font-family: "Montserrat", Arial, sans-serif;
    font-weight: 800;
    font-size: 50px;
    fill: var(--paper);
  }
  .phone-icon { fill: var(--paper); }
</style>
</head>
<body>
<svg class="billboard" viewBox="0 0 1200 347" xmlns="http://www.w3.org/2000/svg">
  <defs>
    <linearGradient id="porch-scene-tones" x1="0" y1="0" x2="1" y2="0">
      <stop offset="0" stop-color="#ffffff"/>
      <stop offset="0.22" stop-color="#e8f1f8"/>
      <stop offset="0.55" stop-color="#cadeef"/>
      <stop offset="1" stop-color="#b9cfe0"/>
    </linearGradient>
    <linearGradient id="porch-scene-depth" x1="0" y1="0" x2="0" y2="1">
      <stop offset="0" stop-color="#f4f6f8" stop-opacity="0.9"/>
      <stop offset="0.45" stop-color="#7badd7" stop-opacity="0.35"/>
      <stop offset="0.7" stop-color="#a9c98a" stop-opacity="0.45"/>
      <stop offset="1" stop-color="#c9c3b8" stop-opacity="0.6"/>
    </linearGradient>
  </defs>

  <!-- porch photo area -->
  <g class="porch-photo" role="img" aria-label="Photo of a bright screened porch with wicker seating, ceiling fans and a potted palm overlooking a lake and lawn">
    <polygon points="600,0 1200,0 1200,268 600,268" fill="url(#porch-scene-tones)"/>
    <polygon points="690,0 1200,0 1200,268 690,268" fill="url(#porch-scene-depth)"/>
  </g>

  <!-- headline band -->
  <polygon class="headline-band" points="0,0 650,0 588,206 0,206"/>
  <polygon class="accent-stripe" points="110,218 588,212 655,0 668,0 598,230"/>

  <text class="headline" x="26" y="122" textLength="560" lengthAdjust="spacingAndGlyphs">Screen Your Porch</text>
  <text class="tagline" x="28" y="184" textLength="540" lengthAdjust="spacingAndGlyphs">BUILT FOR THE COAST</text>

  <!-- company name -->
  <rect class="company-mark" x="28" y="246" width="40" height="40"/>
  <text class="company-name" x="82" y="288" textLength="480" lengthAdjust="spacingAndGlyphs">COASTWISE SCREENING</text>

  <!-- contact band -->
  <polygon class="accent-stripe" points="618,260 760,256 616,266 594,347 590,347"/>
  <polygon class="contact-band" points="620,268 1200,268 1200,347 598,347"/>

  <g class="phone-icon" transform="translate(628,286)">
    <path d="M8 2 C6 2 2 5 2 9 C2 22 16 36 29 36 C33 36 36 32 36 30 L36 26 L28 22 L24 26 C19 24 14 19 12 14 L16 10 L12 2 Z"/>
    <path d="M22 4 A12 12 0 0 1 34 16 L31 16 A9 9 0 0 0 22 7 Z"/>
    <path d="M22 10 A6 6 0 0 1 28 16 L25 16 A3 3 0 0 0 22 13 Z"/>
  </g>
  <text class="phone-number" x="676" y="326" textLength="500" lengthAdjust="spacingAndGlyphs">910.555.0142</text>
</svg>
</body>
</html>
```